BMR Going Cashless

Hello,
We are a medical office looking to get a flyer created to promote to our patients we will be going "Cashless." Our tagline will be "Cash-Less is Stress-Less"

"Starting in July, to offer you the fastest and most convenient service, we are transitioning to a cashless system. You can now enjoy faster checkout times and greater security with card and contactless payments. More info to come."

I've added two other flyers as sample designs we've used.

Please include logo, addresses, website, phone number

Files to include jpeg, png, pdf (under 5mb), Facebook and Instagram sizing.

Thank you,
Lowen

```html
<!DOCTYPE html>
<html lang="en">
<head>
<meta charset="utf-8">
<title>BMR Foot &amp; Ankle – Going Cashless</title>
<link href="https://fonts.googleapis.com/css2?family=Bebas+Neue&family=Poppins:wght@400;500;600;700;800&family=Sacramento&display=swap" rel="stylesheet">
<style>
  :root{
    --charcoal:#333333;
    --charcoal-light:#464646;
    --teal:#55c1a6;
    --teal-deep:#3f8a68;
    --orange:#f27b4a;
    --ink:#2f2f2f;
    --white:#ffffff;
  }
  *{margin:0;padding:0;box-sizing:border-box}
  html,body{width:885px;height:1200px;overflow:hidden;background:var(--charcoal)}
  .flyer{position:relative;width:885px;height:1200px;overflow:hidden;
    background:radial-gradient(circle at 50% 28%,var(--charcoal-light) 0%,var(--charcoal) 60%);
    font-family:"Poppins",sans-serif;color:var(--white)}
  .backdrop{position:absolute;inset:0}
  .brand{position:absolute;top:74px;left:0;width:885px;display:flex;justify-content:center;align-items:center;gap:12px}
  .brand-dot{width:34px;height:34px;border-radius:50%;background:var(--teal)}
  .brand-name{font-family:"Poppins",sans-serif;font-weight:800;font-size:27px;line-height:1;color:var(--orange);letter-spacing:.5px}
  .headline{position:absolute;top:0;left:0}
  .tagline-script{font-family:"Sacramento",cursive;fill:var(--teal)}
  .tagline-bold{font-family:"Bebas Neue",sans-serif;fill:var(--orange)}
  .start-badge{position:absolute;left:224px;top:493px;width:436px;height:77px;background:var(--orange);
    border-radius:6px;box-shadow:0 4px 8px rgba(0,0,0,.3);display:flex;align-items:center;justify-content:center;
    font-weight:700;font-size:54px;letter-spacing:16px;padding-left:16px}
  .start-month{position:absolute;top:574px;left:0;width:885px;text-align:center;font-weight:800;font-size:104px;line-height:1;letter-spacing:-3px}
  .intro{position:absolute;top:700px;left:40px;width:805px;text-align:center;color:#1e1e1e;font-size:21px;line-height:1.25}
  .divider{position:absolute;top:786px;left:47px;width:790px;border-top:1.5px dashed var(--ink)}
  .enjoy{position:absolute;top:812px;left:50px;font-weight:700;font-size:54px;line-height:66px;letter-spacing:-2px}
  .enjoy .accent{color:var(--orange)}
  .split{position:absolute;top:815px;left:344px;height:191px;border-left:1.5px dashed var(--ink)}
  .benefits{position:absolute;top:815px;left:386px;list-style:none}
  .benefits li{display:flex;align-items:center;gap:12px;height:51px;font-weight:600;font-size:25px;color:var(--ink)}
  .more-info{position:absolute;top:980px;left:388px;font-weight:700;font-size:18px;letter-spacing:8.5px}
  .offices{position:absolute;top:1051px;left:50px;display:flex;gap:5px}
  .office{position:relative;width:174px;height:96px;background:var(--charcoal);border-radius:3px;text-align:center;padding-top:22px}
  .office-pin{position:absolute;top:-12px;left:75px}
  .office-name{font-weight:700;font-size:15px;color:var(--teal);line-height:1.2}
  .office-address{font-size:11.2px;line-height:1.3;margin-top:4px}
  .contact{position:absolute;top:1048px;left:600px}
  .contact-label{font-weight:700;font-size:14px;letter-spacing:5px;color:var(--ink)}
  .phone{display:flex;align-items:center;gap:6px;margin-top:6px;font-weight:700;font-size:27px;line-height:1}
  .web-bar{position:absolute;top:1119px;left:598px;width:287px;height:27px;background:var(--orange);
    font-size:16px;letter-spacing:3.2px;padding-left:10px;line-height:27px}
  .web-bar b{font-weight:700}
</style>
</head>
<body>
<main class="flyer">
  <svg class="backdrop" width="885" height="1200" viewBox="0 0 885 1200" aria-hidden="true">
    <circle cx="442" cy="1286" r="754" fill="var(--teal-deep)"/>
    <circle cx="442" cy="1145" r="600" fill="var(--teal)" stroke="var(--charcoal)" stroke-width="2"/>
    <rect x="0" y="740" width="885" height="460" fill="var(--teal)"/>
  </svg>

  <header class="brand">
    <span class="brand-dot"></span>
    <span class="brand-name">BMR FOOT &amp; ANKLE</span>
  </header>

  <svg class="headline" width="885" height="470" viewBox="0 0 885 470">
    <text class="tagline-script" x="88" y="300" font-size="200" textLength="712" lengthAdjust="spacingAndGlyphs">Cash-Less</text>
    <text class="tagline-bold" x="93" y="453" font-size="162" textLength="697" lengthAdjust="spacingAndGlyphs">IS STRESS-LESS</text>
  </svg>

  <div class="start-badge">STARTING</div>
  <div class="start-month">IN JULY</div>

  <p class="intro">To offer you the fastest and most convenient service, we are transitioning to a cashless system</p>
  <div class="divider"></div>

  <h2 class="enjoy">YOU CAN<br><span class="accent">NOW<br>ENJOY</span></h2>
  <div class="split"></div>

  <ul class="benefits">
    <li><svg width="22" height="22" viewBox="0 0 22 22"><circle cx="11" cy="11" r="11" fill="var(--orange)"/><path d="M6 11.5l3.3 3.3L16 8" fill="none" stroke="#fff" stroke-width="2.2" stroke-linecap="round" stroke-linejoin="round"/></svg>Faster checkout times</li>
    <li><svg width="22" height="22" viewBox="0 0 22 22"><circle cx="11" cy="11" r="11" fill="var(--orange)"/><path d="M6 11.5l3.3 3.3L16 8" fill="none" stroke="#fff" stroke-width="2.2" stroke-linecap="round" stroke-linejoin="round"/></svg>Greater security with card</li>
    <li><svg width="22" height="22" viewBox="0 0 22 22"><circle cx="11" cy="11" r="11" fill="var(--orange)"/><path d="M6 11.5l3.3 3.3L16 8" fill="none" stroke="#fff" stroke-width="2.2" stroke-linecap="round" stroke-linejoin="round"/></svg>Contactless payments</li>
  </ul>
  <p class="more-info">MORE INFO TO COME....</p>

  <section class="offices">
    <article class="office">
      <svg class="office-pin" width="24" height="24" viewBox="0 0 24 24"><circle cx="12" cy="12" r="12" fill="var(--orange)"/><path d="M12 5.5a4 4 0 0 0-4 4c0 3 4 8 4 8s4-5 4-8a4 4 0 0 0-4-4z" fill="#fff"/><circle cx="12" cy="9.5" r="1.5" fill="var(--orange)"/></svg>
      <h3 class="office-name">Northgate Office</h3>
      <p class="office-address">210 Alder Ridge Rd.<br>Suite 140 Northgate,<br>MD 20915</p>
    </article>
    <article class="office">
      <svg class="office-pin" width="24" height="24" viewBox="0 0 24 24"><circle cx="12" cy="12" r="12" fill="var(--orange)"/><path d="M12 5.5a4 4 0 0 0-4 4c0 3 4 8 4 8s4-5 4-8a4 4 0 0 0-4-4z" fill="#fff"/><circle cx="12" cy="9.5" r="1.5" fill="var(--orange)"/></svg>
      <h3 class="office-name">Riverside Office</h3>
      <p class="office-address">58 Mill Creek Lane<br>Riverside, WV 25830</p>
    </article>
    <article class="office">
      <svg class="office-pin" width="24" height="24" viewBox="0 0 24 24"><circle cx="12" cy="12" r="12" fill="var(--orange)"/><path d="M12 5.5a4 4 0 0 0-4 4c0 3 4 8 4 8s4-5 4-8a4 4 0 0 0-4-4z" fill="#fff"/><circle cx="12" cy="9.5" r="1.5" fill="var(--orange)"/></svg>
      <h3 class="office-name">Hillcrest Office</h3>
      <p class="office-address">4475 Copper Hill Blvd.<br>Suite 305 Hillcrest,<br>MD 20940</p>
    </article>
  </section>

  <section class="contact">
    <p class="contact-label">CONTACT US TODAY</p>
    <p class="phone">
      <svg width="26" height="26" viewBox="0 0 26 26"><circle cx="13" cy="13" r="13" fill="var(--orange)"/><path d="M9.2 7c.5 0 .9.3 1 .8l.6 2.2c.1.4 0 .8-.3 1.1l-1 .9a8 8 0 0 0 4.6 4.6l.9-1c.3-.3.7-.4 1.1-.3l2.2.6c.5.1.8.5.8 1v1.6c0 .6-.5 1.1-1.1 1.1A12 12 0 0 1 6.5 8.1C6.5 7.5 7 7 7.6 7z" fill="#fff"/></svg>
      (555) 014-2290
    </p>
  </section>
  <p class="web-bar">www.<b>bmrfootcare</b>.com</p>
</main>
</body>
</html>
```